Morvane Capital, a private equity fund, needs a brochure

Morvane Capital is a private equity fund dedicated to the development of budget hotels in France (reasonably priced hotel rooms).
Our customers are French private and high-income investors.

The brochure should communicate :
- seriousness and expertise
- trust, confidence and security
- financial product and profitability

The title is : Investissez dans l'hôtellerie économique et l'immobilier

Brochure size :
3 pages A4
Open size : 63 x 29,7 cm
Closed size : 21 x 29,7 cm

Our competitors :
Trelisse http://trelisse-immo-horizon.example/
789 Parcours http://www.789parcours.example/
GLD Capital http://www.gldam.example/
Soltane capital http://www.soltanecapital.example/
Barostel http://www.barostel.example/

Target Market(s)

Private investors, high-income ; Institutional investors ; Target customers are French private investors with high revenue.

Industry/Entity Type

Financial

Requirements
Must have
• - Brochure must respect our identity (you can see our logo) and use its colors and typo (and/or same typo style)
- You must use pictures on each interior pages (pictures of projetc and hotels)

```html
<!DOCTYPE html>
<html lang="fr">
<head>
<meta charset="utf-8">
<title>Morvane Capital – Hôtellerie économique</title>
<link href="https://fonts.googleapis.com/css2?family=Arimo:wght@400;700&family=PT+Sans+Narrow:wght@700&family=PT+Serif:wght@400;700&display=swap" rel="stylesheet">
<style>
:root{
  --backdrop:#3b4347;
  --paper:#cfd5d8;
  --ink:#3a3a3a;
  --ink-strong:#161616;
  --accent:#c0262b;
  --sidebar-top:#a11d22;
  --sidebar-mid:#c7282d;
  --on-accent:#ffffff;
  --gold-dark:#b08a2e;
  --gold-light:#d9bc6a;
}
*{margin:0;padding:0;box-sizing:border-box}
html,body{width:900px;height:1200px;overflow:hidden;background:var(--backdrop)}
.page{position:absolute;left:52px;top:48px;width:786px;height:1109px;background:var(--paper);overflow:hidden;font-family:"Arimo",Arial,sans-serif;color:var(--ink)}
.main{position:absolute;left:38px;top:75px;width:482px;font-size:12.3px;line-height:16px;text-align:justify;hyphens:auto;-webkit-hyphens:auto}
.main p{margin-bottom:16px}
.main h2{font-family:"PT Sans Narrow",sans-serif;font-weight:700;color:var(--accent);font-size:15.5px;line-height:17px;margin:0 0 15px;text-align:left}
.points{list-style:none;margin-bottom:14px;font-weight:700;color:var(--ink-strong);font-size:12px;line-height:16px}
.points li::before{content:"";display:inline-block;width:7px;height:7px;background:var(--accent);margin-right:8px}
.sidebar{position:absolute;left:549px;top:0;width:237px;height:644px;background:linear-gradient(180deg,var(--sidebar-top),var(--sidebar-mid) 40%,var(--sidebar-top));color:var(--on-accent);padding:80px 40px 0 14px}
.sidebar h3{font-family:"PT Serif",serif;font-weight:700;font-size:15.5px;line-height:17px;margin-bottom:21px}
.sidebar p{font-family:"PT Serif",serif;font-size:12.4px;line-height:15.9px;margin-bottom:18px}
.sidebar ul{list-style:none;font-weight:700;font-size:11.8px;line-height:16px;margin-right:-12px;text-align:justify}
.sidebar li{margin-bottom:16px}
.sidebar li::before{content:"";display:inline-block;width:7px;height:7px;background:var(--on-accent);margin-right:8px}
.key-visual{position:absolute;left:612px;top:628px;width:96px;height:240px;background:linear-gradient(180deg,var(--gold-light),var(--gold-dark))}
.project{position:absolute;top:884px;width:196px;height:108px;border:1px solid #fff}
.p1{left:42px;background:linear-gradient(180deg,#7aa4c8,#8a6f55 70%,#5f6b45)}
.p2{left:296px;background:linear-gradient(180deg,#6f9ec7,#c9a86a 60%,#7c7a6d)}
.p3{left:549px;background:linear-gradient(180deg,#9aa7a5,#8b8e86 60%,#6e7668)}
.caption{position:absolute;top:1004px;width:200px;font-size:10px;line-height:16px;color:var(--ink-strong)}
.caption b{font-weight:700}
</style>
</head>
<body>
<div class="page">
  <section class="main">
    <p>L’activité de Morvane Capital est notamment centrée sur l’investissement dans des sociétés développant une activité commerciale d’exploitation d’hôtels économiques. Ces sociétés du portefeuille seront à terme propriétaires des actifs immobiliers qu’elles exploitent.</p>
    <p>Morvane Capital pourra également diversifier ses investissements dans les secteurs de la promotion immobilière et de l’immobilier de service (meublés de tourisme et/ou résidences médicalisées).</p>
    <h2>Immobilier, valeur refuge pour l’investisseur<br>(selon l’analyse de Morvane Capital)</h2>
    <ul class="points">
      <li>Un investissement dans la pierre.</li>
      <li>Une réponse à l’incertitude des marchés financiers et de la monnaie et des risques d’inflation..</li>
      <li>Des emplacements exceptionnels (centres villes, aéroports, zones commerciales).</li>
    </ul>
    <h2>Un partenariat avec ARCELUNE HOTELS GROUP</h2>
    <p>Pour l’exploitation des investissements hôteliers, les sociétés du portefeuille interviendront en partenariat avec un opérateur hôtelier – ARCELUNE HOTELS GROUP – dans le cadre d’un accord de franchise (Arcelune Hotels Group, 2ème opérateur d’Europe, plus de 1000 hôtels dans le monde).</p>
    <ul class="points">
      <li>Contrats de franchise sous enseignes:<br>Étape Première **, Clocheval *** et Lysandre Inn ***.</li>
      <li>Contrats d’assistante technique.</li>
      <li>Implantation de plus de 12 hôtels dans 6 régions françaises d’outremer.</li>
    </ul>
    <h2>Focus sur l’hôtellerie économique<br>dans les régions françaises ultramarines</h2>
    <p>Le marché des hôtels économiques normés et standardisés sous enseigne nationale ou internationale est peu développé dans les DOM-COM. Ces régions sont équipées principalement d’hôtels balnéaires à vocation touristique essentiellement implantés sur des lieux généralement éloignés des centres économiques. Depuis une vingtaine d’années, le développement important des populations et la centralisation des zones commerciales et industrielles sur les capitales administratives ont généré d’importants embouteillages qui compliquent les accès à ces zones. L’offre hôtelière n’est plus en adéquation avec les attentes des visiteurs professionnels. La création d’une chaine d’hôtels économiques est la réponse à ce besoin et bénéficie de l’appui de la puissance publique et des instances régionales.</p>
    <ul class="points">
      <li>Absence d’hôtels économiques standardisés et normés dans ces régions.</li>
      <li>Structures hôtelières existantes inadaptées aux besoins du marché professionnel et coûteuses : prix des nuitées proposées par ces nouveaux hôtels inférieurs de 30 à 50% aux prix pratiqués localement.</li>
      <li>Programmes d’investissements bénéficiant d’avantages fiscaux, sociaux et de subventions.</li>
    </ul>
  </section>

  <aside class="sidebar">
    <h3>Pourquoi l’hôtellerie<br>et l’immobilier?</h3>
    <p>Dans des conditions économiques et financières perturbées depuis la crise financière de 2008, les investisseurs exigent aujourd’hui des placements structurés pour résister aux effets économiques induits. Selon l’analyse des équipes de Morvane Capital, le marché de l’hôtellerie économique en croissance depuis sa création répond particulièrement bien à ces attentes. Ce positionnement est en adéquation avec la baisse des budgets alloués aux déplacements et voyages professionnels et touristiques.</p>
    <ul>
      <li>Le marché de l’immobilier reste quant à lui une valeur refuge en temps de crise, selon l’analyse des équipes de Morvane Capital.</li>
      <li>Un marché en croissance malgré la crise.</li>
      <li>Sur 2011, la croissance cumulée du nombre de nuitées atteint + 3,2% par rapport à 2010. (source Veridane)</li>
    </ul>
  </aside>

  <div class="key-visual" role="img" aria-label="Photo de clés d’hôtel sur un porte-clés doré"></div>

  <div class="project p1" role="img" aria-label="Vue d’un hôtel Lysandre Inn à Sainte-Clotilde"></div>
  <div class="project p2" role="img" aria-label="Vue d’un hôtel Étape Première à Saint-Pierre"></div>
  <div class="project p3" role="img" aria-label="Perspective aérienne d’un hôtel Étape Première à Pointe-à-Pitre"></div>
  <p class="caption" style="left:42px"><b>Réunion -</b> Sainte-Clotide Lysandre Inn,<br>100 chambres</p>
  <p class="caption" style="left:296px"><b>Réunion -</b> Saint-Pierre Étape Première,<br>100 chambres</p>
  <p class="caption" style="left:549px"><b>Guadeloupe -</b> Pointe à Pitre-Bergevin<br>Étape Première, 100 chambres</p>
</div>
</body>
</html>
```